Flyer for Medical practice welcoming new patients

We need a DL size brochure designed for Medical practice to advertise that we are accepting new patients. Our practice has special interests in women's and children's health and seniors health. Our existing advertising materials are in the colour scheme of purples I have uploaded our logo which includes our colour scheme.

Target Market(s)

Versatile to target anyone looking for a small medical practice that offers continuous care of seeing the same Doctor every time

Industry/Entity Type

Advertising

Font styles to use
Serif

Colors
6b449b
876aae
b7a5cc

Requirements
Must have
• The practice logo of just the picture not Dr Petra Holcombe.
• Purple colour scheme.
• Practice name: Tarrabeen Medical Practice.
• Address: 147 Corlett Rd, Tarrabeen NSW 2500.
• Phone: 4871 6035.
• DL size brochure
• Welcoming new patients ( a strong emphasis needs to be placed on this)
• Nurse and onsite ECG's and lung function tests.
• Travel vaccines including yellow fever
• Bulk billing for tertiary students
• We would also like design to alter the text so that we can change the points to be reflect who we are targeting at the time.
Nice to have
• The practice logo with Dr Petra Holcombe somewhere not as a feature as the practice no longer goes under this name but is still well known as Dr Holcombe's.

```html
<!DOCTYPE html>
<html lang="en">
<head>
<meta charset="utf-8">
<title>Tarrabeen Medical Practice – New Patients Flyer</title>
<link rel="stylesheet" href="https://fonts.googleapis.com/css2?family=Open+Sans:wght@400;600&family=Arimo:wght@400;700&display=swap">
<style>
  :root {
    --purple-deep: #6b449b;
    --purple-mid: #876aae;
    --purple-soft: #a893c8;
    --lilac: #c9a6cc;
    --lilac-pale: #e6d8ec;
    --ink-heading: #5e3a92;
    --white: #ffffff;
    --backdrop: #d9d9d9;
  }
  html, body {
    margin: 0;
    padding: 0;
    width: 1200px;
    height: 1000px;
    overflow: hidden;
    background: var(--backdrop);
  }
  .canvas {
    position: relative;
    width: 1200px;
    height: 1000px;
  }
  .flyer {
    position: absolute;
    left: 347px;
    top: 37px;
    width: 440px;
    height: 925px;
    display: block;
  }
  .brand-name {
    font-family: "Open Sans", sans-serif;
    font-weight: 600;
    font-size: 21px;
    fill: var(--purple-deep);
  }
  .headline {
    font-family: "Arimo", sans-serif;
    fill: var(--ink-heading);
    text-anchor: middle;
  }
  .headline-lead { font-size: 25px; letter-spacing: 5px; }
  .headline-main { font-size: 39px; }
  .headline-hero { font-size: 62px; font-weight: 700; }
  .service-point {
    font-family: "Open Sans", sans-serif;
    font-size: 18.5px;
    fill: var(--white);
  }
  .contact-title {
    font-family: "Arimo", sans-serif;
    font-weight: 700;
    font-size: 15px;
    fill: var(--ink-heading);
  }
  .contact-line {
    font-family: "Arimo", sans-serif;
    font-size: 16.5px;
    fill: var(--white);
  }
  .contact-label { font-weight: 700; }
</style>
</head>
<body>
<main class="canvas">
  <svg class="flyer" viewBox="0 0 440 925" xmlns="http://www.w3.org/2000/svg" aria-label="Tarrabeen Medical Practice new patients flyer">
    <defs>
      <linearGradient id="panel-gradient" x1="0" y1="0" x2="0" y2="1">
        <stop offset="0" stop-color="var(--purple-deep)"/>
        <stop offset="0.55" stop-color="var(--purple-mid)"/>
        <stop offset="1" stop-color="var(--purple-soft)"/>
      </linearGradient>
    </defs>

    <!-- backdrop panel -->
    <rect class="panel" width="440" height="925" fill="url(#panel-gradient)"/>

    <!-- lower-left white tab -->
    <path class="corner-tab" d="M0,405 C12,495 55,552 130,562 L0,562 Z" fill="var(--white)"/>

    <!-- main white sweep -->
    <path class="white-sweep" d="M165,0 C70,50 22,170 28,295 C34,445 150,565 300,612 C350,628 400,645 440,658 L440,0 Z" fill="var(--white)"/>

    <!-- lilac crescent -->
    <path class="lilac-crescent" d="M55,175 C30,305 72,462 200,560 C282,602 362,612 440,612 L440,632 C340,632 250,604 168,556 C58,480 32,320 55,175 Z" fill="var(--lilac)"/>

    <!-- practice name -->
    <circle class="brand-dot" cx="167" cy="106" r="62" fill="var(--lilac-pale)"/>
    <text class="brand-name" x="244" y="105">Tarrabeen</text>
    <text class="brand-name" x="244" y="134">Medical Practice</text>

    <!-- headline -->
    <text class="headline headline-lead" x="266" y="284">WE ARE NOW</text>
    <text class="headline headline-main" x="266" y="328" textLength="318" lengthAdjust="spacingAndGlyphs">ACCEPTING NEW</text>
    <text class="headline headline-hero" x="266" y="388" textLength="322" lengthAdjust="spacingAndGlyphs">PATIENTS!</text>

    <!-- service points -->
    <g class="service-list">
      <circle cx="15" cy="687" r="4.5" fill="var(--white)"/>
      <text class="service-point" x="23" y="694">Nurse on site for ECG's, lung function tests,</text>
      <text class="service-point" x="23" y="719">health assessments and much more</text>

      <circle cx="15" cy="752" r="4.5" fill="var(--white)"/>
      <text class="service-point" x="23" y="759">We offer travel vaccines including yellow fever</text>

      <circle cx="15" cy="795" r="4.5" fill="var(--white)"/>
      <text class="service-point" x="23" y="802">Bulk billing for tertiary students</text>
    </g>

    <!-- contact details -->
    <g class="contact">
      <text class="contact-title" x="12" y="855">CONTACT DETAILS:</text>
      <text class="contact-line" x="14" y="884"><tspan class="contact-label">Address:</tspan> 147 Corlett Rd, Tarrabeen NSW 2500</text>
      <text class="contact-line" x="14" y="908"><tspan class="contact-label">Telephone:</tspan> 4871 6035</text>
    </g>
  </svg>
</main>
</body>
</html>
```